Valdane Companies Business Card Design

We need a new business card for our Private Equity Real Estate Development firm, “Valdane” and our EB-5 regional center “Thornmere Regional Center” on one card. We prefer a design that is simple, elegant, and represents the luxury products we design and build as well as the financial security and stability our successful history has produced. We are an industry leader in our field and 3rd generation family business that has evolved into an institutional quality investment platform. Considered design size is standard business card dimensions (3.5 x 2 inches with an additional 1/8 inch space for design elements or backgrounds that extend beyond the finished size of your piece.

Target Market(s)

• High net worth individuals
• Highly skilled technical workers and physicians in the US seeking investment-based immigration opportunities
• Sophisticated private equity investors
• Intermediary partners include domestic attorneys and investment brokers, as well as international agent networks
• US real estate developers

Industry/Entity Type

Finance

Contact Information for Business Card

(Providing placeholder info for personal information, please design for longer character spaces, longer names and addresses etc..)
• Logo for Valdane
• Logo for Thornmere Regional Center
• Full name: Marcus Valdane
• Job title: CEO
• Email address: mvaldane@valdanecompanies.com
• Cell phone number: +1.555.314.2287
• Office number +1.555.628.4410
• Office address: Larkfield Court 5, 4817 Vista Orilla, Harrowgate, CR.
• Website: www.valdanecompanies.com

Font styles to use
Serif
Sans Serif

Colors
ec1f27
ffffff
000000

Requirements
Must have
• • Logo for Valdane
• • Logo for Thornmere Regional Center
• - Use rounded corners
• (See .ai file included for logos)
Nice to have
• • Simple, elegant design
• • Aesthetically compatible with our website design (www.valdanecompanies.com)
• • Color palette including but not limited to white, black, and red (as per logos)
Should not have
• - Not too much red color
• - Do not stack both logos on top of each other

```html
<!DOCTYPE html>
<html lang="en">
<head>
<meta charset="utf-8">
<title>Valdane Companies Business Card</title>
<link href="https://fonts.googleapis.com/css2?family=Cinzel:wght@600;700&family=Lato:wght@400&display=swap" rel="stylesheet">
<style>
  :root {
    --backdrop: #646464;
    --card: #2f2f2f;
    --ink: #ffffff;
    --ink-soft: #e6e6e6;
    --mark: #9a9a9a;
    --mark-fill: #b9b9b9;
    --rule: #5a5a5a;
    --icon: #d9d9d9;
  }
  * { margin: 0; padding: 0; box-sizing: border-box; }
  html, body {
    width: 1200px; height: 1200px; overflow: hidden;
    background: var(--backdrop);
  }
  .card {
    position: absolute;
    left: 246px;
    width: 708px; height: 404px;
    background: var(--card);
    border-radius: 24px;
    box-shadow: 0 10px 22px rgba(0,0,0,0.28);
  }
  .card--front { top: 138px; }
  .card--back { top: 646px; }

  .brand {
    position: absolute;
    display: flex; align-items: center; gap: 16px;
    font-family: "Cinzel", serif; font-weight: 600;
    white-space: nowrap;
  }
  .brand__square { display: block; background: var(--mark-fill); }

  .brand--front {
    left: 50%; top: 202px; transform: translate(-50%, -50%);
    font-size: 40px; letter-spacing: 1px; color: var(--mark);
  }
  .brand--front .brand__square { width: 46px; height: 46px; }

  .brand--back {
    right: 37px; top: 50px;
    font-size: 19px; letter-spacing: 1px; color: var(--ink);
  }
  .brand--back .brand__square { width: 44px; height: 44px; }

  .person__name {
    position: absolute; left: 36px; top: 196px;
    font-family: "Cinzel", serif; font-weight: 700;
    font-size: 27px; line-height: 1; color: var(--ink);
    letter-spacing: 0.5px;
  }
  .person__title {
    position: absolute; left: 37px; top: 232px;
    font-family: "Lato", sans-serif; font-size: 19px;
    line-height: 1; color: var(--ink-soft);
  }
  .divider {
    position: absolute; left: 36px; right: 37px; top: 263px;
    height: 2px; background: var(--rule);
  }
  .contacts {
    position: absolute; left: 42px; top: 276px;
    list-style: none;
    font-family: "Lato", sans-serif; font-size: 17px; color: var(--ink-soft);
  }
  .contacts li {
    display: flex; align-items: center; height: 23.3px;
  }
  .contacts svg { width: 14px; height: 14px; margin-right: 12px; flex: none; }
  .address {
    position: absolute; right: 37px; top: 323px;
    text-align: right; font-style: normal;
    font-family: "Lato", sans-serif; font-size: 17px; line-height: 23.5px;
    color: var(--ink-soft);
  }
</style>
</head>
<body>
  <section class="card card--front">
    <div class="brand brand--front">
      <span class="brand__square"></span>
      <span class="brand__name">Valdane Capital</span>
    </div>
  </section>

  <section class="card card--back">
    <div class="brand brand--back">
      <span class="brand__square"></span>
      <span class="brand__name">Thornmere Regional Center</span>
    </div>

    <h1 class="person__name">MARCUS VALDANE</h1>
    <p class="person__title">CEO</p>
    <div class="divider"></div>

    <ul class="contacts">
      <li>
        <svg viewBox="0 0 16 16" aria-hidden="true"><path fill="var(--icon)" d="M3.5 1l2.5 3-1.4 1.6c.9 2.3 2.5 3.9 4.8 4.8L11 9l3 2.5-1.6 2.9C7 14 2 9 1.6 3.6z"/></svg>
        +1.555.314.2287
      </li>
      <li>
        <svg viewBox="0 0 16 16" aria-hidden="true"><rect x="4" y="1" width="8" height="14" rx="1.5" fill="none" stroke="var(--icon)" stroke-width="1.4"/><circle cx="8" cy="12.5" r="0.9" fill="var(--icon)"/></svg>
        +1.555.628.4410
      </li>
      <li>
        <svg viewBox="0 0 16 16" aria-hidden="true"><rect x="1" y="3" width="14" height="10" fill="var(--icon)"/><path d="M1 3l7 6 7-6" fill="none" stroke="var(--card)" stroke-width="1.3"/></svg>
        mvaldane@valdanecompanies.com
      </li>
      <li>
        <svg viewBox="0 0 16 16" aria-hidden="true"><g fill="none" stroke="var(--icon)" stroke-width="1.1"><circle cx="8" cy="8" r="6.5"/><ellipse cx="8" cy="8" rx="3" ry="6.5"/><path d="M1.5 8h13M2.5 4.8h11M2.5 11.2h11"/></g></svg>
        www.valdanecompanies.com
      </li>
    </ul>

    <address class="address">
      Larkfield Court 5, 4817 Vista Orilla<br>
      Harrowgate, CR
    </address>
  </section>
</body>
</html>
```